Verdora Cookbook Cover

I need a design (front and back) for a cookbook cover. Our partners are looking for a few ideas to pick from.
You can see the style for one of the cookbooks we currently carry - uploaded with this brief.
This cookbook is a little different than most cookbooks out there. It is a cancer-fighting cookbook but we don't want it to be so cancer focused that people who don't have cancer will not buy. The book starts out with a section for Foods that Help, then goes to another section called Foods that Hurt. Then, we provide a Recipes section from the ingredients found in Foods that Help. Finally, the last section is called Beyond the Plate and deals with healthy lifestyle habits. You can see a rough draft of the content of the book at the link below. Please keep in mind that the current covers you see are not at all what we want. These were just put there to fill in the space.
Link for cookbook content: https://www.filecrate-share.com/s/4kq92xpwt7bnrvd/The%20Sunlit%20Table%20-%20EDITED.pdf?dl=0
The title: The Sunlit Table
Subtitle: Eating Brighter One Meal at a Time
Author: Mirela Tosk
The company that puts the book out is Verdora. It would be nice to have the logo somewhere small. Logo can be found here: https://www.filecrate-share.com/s/mz83ntbq2vhxe5a/Verdora%20Logo%20%26%20Guidelines.zip?dl=0
Like "Bring Home a Brighter Bowl" attached to this brief, we do NOT want something somber but more on the bright side. Just make it look nice and fresh. It would also be nice to somehow incorporate the concept of the cancer ribbon or a silhouette of it in a way that is not upfront but can still be acknowledge. No need for it to be pink and if that does not work, than it's better just to leave it out.
For the back cover, you can design it but simply leave room for us to fill in some text. No need for a spine design as it will be spiral bound.
The file must be designed and saved in PHOTOSHOP format.
According to the designer, the dimensions are:
207mm x 270mm + 5mm bleed
If you want to use the recipe pictures somehow in the cover, just snatch a picture from the content PDF and we can always replace it with the original larger file at a later time. Unfortunately, I don't have the pictures uploaded in filecrate.

```html
<!DOCTYPE html>
<html lang="en">
<head>
<meta charset="utf-8">
<title>Verdora Cookbook Cover – The Sunlit Table</title>
<link rel="stylesheet" href="https://fonts.googleapis.com/css2?family=Abril+Fatface&family=Open+Sans:wght@400;600&display=swap">
<style>
  :root {
    --stage: #e4e4e4;
    --slate: #2f3031;
    --slate-light: #3b3c3d;
    --leaf: #7cc242;
    --paper: #ffffff;
  }
  * { box-sizing: border-box; margin: 0; padding: 0; }
  html, body {
    width: 1200px; height: 790px; overflow: hidden;
    background: var(--stage);
  }
  .cover {
    position: absolute;
    left: 316px; top: 25px;
    width: 568px; height: 740px;
    background: radial-gradient(ellipse at 50% 40%, var(--slate-light), var(--slate) 70%);
    box-shadow: 0 8px 24px rgba(0,0,0,0.25);
    overflow: hidden;
  }
  .title {
    position: absolute; inset: 0;
    font-family: "Abril Fatface", serif;
    font-weight: 400;
    line-height: 1;
  }
  .title span { position: absolute; white-space: nowrap; }
  .title-the {
    left: 44px; top: 62px;
    color: var(--paper); font-size: 34px;
  }
  .title-sunlit {
    left: 36px; top: 90px;
    color: var(--leaf); font-size: 94px;
  }
  .title-table {
    left: 292px; top: 148px;
    color: var(--paper); font-size: 94px;
  }
  .subtitle {
    position: absolute; left: 112px; top: 256px;
    font-family: "Open Sans", sans-serif; font-weight: 400;
    font-size: 18px; color: var(--paper);
    padding-bottom: 4px;
    border-bottom: 1px solid var(--leaf);
    white-space: nowrap;
  }
  .food-wheel {
    position: absolute; left: 104px; top: 296px;
    width: 360px; height: 340px;
  }
  .imprint {
    position: absolute; right: 30px; top: 580px;
    display: flex; align-items: center; gap: 8px;
  }
  .imprint-dot {
    width: 22px; height: 22px; border-radius: 50%;
    background: var(--leaf);
  }
  .imprint-name {
    font-family: "Open Sans", sans-serif; font-weight: 600;
    font-size: 20px; color: var(--leaf);
  }
  .author {
    position: absolute; left: 0; right: 0; top: 660px;
    text-align: center;
    font-family: "Open Sans", sans-serif; font-weight: 400;
    font-size: 32px; letter-spacing: 9px; color: var(--leaf);
  }
</style>
</head>
<body>
  <main class="cover">
    <h1 class="title">
      <span class="title-the">The</span>
      <span class="title-sunlit">Sunlit</span>
      <span class="title-table">Table</span>
    </h1>
    <p class="subtitle">Eating Brighter One Meal at a Time</p>

    <svg class="food-wheel" viewBox="0 0 360 340" role="img"
         aria-label="Photograph: white spoons arranged in a ring, each holding a healthy food such as garlic, tomatoes, greens, seeds, nuts, berries, carrots and celery">
      <defs>
        <radialGradient id="wheel-tones" cx="50%" cy="50%" r="50%">
          <stop offset="0%" stop-color="#2f3031"/>
          <stop offset="30%" stop-color="#2f3031"/>
          <stop offset="42%" stop-color="#e9e6e0"/>
          <stop offset="70%" stop-color="#c9874f"/>
          <stop offset="100%" stop-color="#8f9a52"/>
        </radialGradient>
      </defs>
      <circle cx="180" cy="170" r="168" fill="url(#wheel-tones)"/>
    </svg>

    <div class="imprint">
      <span class="imprint-dot"></span>
      <span class="imprint-name">Verdora</span>
    </div>

    <p class="author">MIRELA TOSK</p>
  </main>
</body>
</html>
```